Business Card Design needed for start up company Halvora

In need of a new business card designed for a start up company based in Sydney, Halvora is a new start up innovative Company, our mission it to make property accessible for everyday Australian and to become the leading Real Estate platform in Australia. We want it to be fresh and clean.

Industry/Entity Type

Financial

Contact Information for Business Card

Section for Name
Section for Title

HALVORA - The Strength of Pooling
Mobile:
Direct:

Font styles to use
Sans Serif

Colors
33a6d7
0692cd
0255a3
ffffff

Requirements
Must have
• Logo, all business card details

```html
<!DOCTYPE html>
<html lang="en">
<head>
<meta charset="utf-8">
<title>Halvora Business Card</title>
<link rel="stylesheet" href="https://fonts.googleapis.com/css2?family=Jost:wght@300;400;500;600;700&display=swap">
<style>
  :root {
    --backdrop: #2b2b2b;
    --paper: #f4f4f4;
    --navy: #21427a;
    --sky: #27a0db;
    --ink: #4a4a4a;
    --rule: #8a8a8a;
    --white: #ffffff;
  }
  * { margin: 0; padding: 0; box-sizing: border-box; }
  html, body { width: 1200px; height: 960px; overflow: hidden; }
  body {
    background: var(--backdrop);
    position: relative;
    font-family: "Jost", Arial, sans-serif;
  }
  .card {
    position: absolute;
    width: 600px;
    height: 342px;
    border-radius: 18px;
    overflow: hidden;
  }
  .card-front { left: 302px; top: 124px; background: var(--paper); }
  .card-back { left: 299px; top: 493px; background: var(--navy); }

  .brand-name { position: absolute; font-weight: 700; line-height: 1; letter-spacing: 0.5px; }

  .card-front .brand-name {
    right: 32px; top: 71px; transform: translateY(-50%);
    font-size: 44px; color: var(--navy);
  }
  .card-back .brand-name {
    left: 50%; top: 172px; transform: translate(-50%, -50%);
    font-size: 62px; color: var(--white);
  }

  .person { position: absolute; left: 29px; top: 180px; }
  .person-name { font-size: 22px; font-weight: 600; color: var(--navy); line-height: 1.1; }
  .person-title { font-size: 15px; font-weight: 400; color: var(--sky); margin-top: 2px; }

  .divider { position: absolute; left: 29px; right: 32px; top: 233px; height: 1px; background: var(--rule); }

  .contact-list { position: absolute; left: 29px; top: 245px; list-style: none; }
  .contact-list li { display: flex; align-items: center; font-size: 14.5px; font-weight: 400; color: var(--ink); height: 20px; }
  .contact-list svg { width: 13px; height: 13px; margin-right: 8px; fill: var(--navy); }

  .address { position: absolute; right: 32px; top: 245px; text-align: right; font-size: 14.5px; font-weight: 400; font-style: normal; color: var(--ink); line-height: 20px; }

  .footer-band { position: absolute; left: 0; bottom: 0; width: 600px; height: 32px; }
  .tagline {
    position: absolute; right: 20px; bottom: 5px;
    font-size: 15px; font-weight: 400; color: var(--white);
  }
</style>
</head>
<body>

<section class="card card-front">
  <span class="brand-name">HALVORA</span>

  <div class="person">
    <p class="person-name">MARA QUINLAN</p>
    <p class="person-title">CEO/FOUNDER</p>
  </div>

  <div class="divider"></div>

  <ul class="contact-list">
    <li><svg viewBox="0 0 24 24"><path d="M6.6 10.8a15.1 15.1 0 0 0 6.6 6.6l2.2-2.2a1 1 0 0 1 1-.25 11.4 11.4 0 0 0 3.6.57 1 1 0 0 1 1 1V20a1 1 0 0 1-1 1A17 17 0 0 1 3 4a1 1 0 0 1 1-1h3.5a1 1 0 0 1 1 1 11.4 11.4 0 0 0 .57 3.6 1 1 0 0 1-.25 1z"/></svg>555 210 4471</li>
    <li><svg viewBox="0 0 24 24"><path d="M7 1h10a2 2 0 0 1 2 2v18a2 2 0 0 1-2 2H7a2 2 0 0 1-2-2V3a2 2 0 0 1 2-2zm0 3v14h10V4zm5 15.2a1.2 1.2 0 1 0 0 2.4 1.2 1.2 0 0 0 0-2.4z"/></svg>555 382 9016</li>
    <li><svg viewBox="0 0 24 24"><path d="M2 5h20v14H2zm2 2v.5l8 5 8-5V7zm0 2.9V17h16V9.9l-8 5z"/></svg>mara@halvora.com</li>
  </ul>

  <address class="address">
    1290 Larkspur Row<br>
    Hobart, Tasmania 72019<br>
    www.halvora.com
  </address>

  <svg class="footer-band" viewBox="0 0 600 32" aria-hidden="true">
    <rect x="0" y="6" width="600" height="8" fill="var(--sky)"/>
    <rect x="0" y="14" width="600" height="18" fill="var(--navy)"/>
    <path d="M384 14 C394 14 396 0 408 0 H600 V32 H384 Z" fill="var(--navy)"/>
  </svg>
  <p class="tagline">The Strength of Pooling</p>
</section>

<section class="card card-back">
  <span class="brand-name">HALVORA</span>
</section>

</body>
</html>
```